Flat bootstrap design for existing site

I'm looking for a modern flat design based around an existing logo. This has to be a custom design (no external templates), and implemented into a bootstrap framework.

The logo is attached as 2 versions - choose whichever you want, that flows better with whatever design you choose.

Added screenshots of the existing site (currently using the default bootstrap layouts). Please make your designs around those pages in the screenshots (i.e. the homepage only has the postal code input and the header). The active page has 3 screenshots, because I wanted to illustrate the other states that would be visible (in the table rows).

This is a moving/junk removal website, just for some context.

Here's some example websites (flat designs) that I like, just to give you an idea of what I'm after.

https://www.plimvora.com/
https://dacklow.com/
https://trevanu.com/
https://quobrintal.com/en/

Coding

Coded - Design and coding required

Number of Pages Required

5+ page

Colors

Designer to choose colors to be used in the design.

Requirements
Must have
• It must be a modern/simple flat design, that is built around the existing logo (attached).
• It has to be implemented using bootstrap.

```html
<!DOCTYPE html>
<html lang="en">
<head>
<meta charset="utf-8">
<title>Haulvane – Booking Details</title>
<link href="https://fonts.googleapis.com/css2?family=Raleway:ital,wght@0,400;0,500;0,600;0,700;1,400;1,500&display=swap" rel="stylesheet">
<style>
:root{
  --brand:#4bc8f4;
  --brand-soft:#93e3fc;
  --page:#ebebeb;
  --white:#ffffff;
  --field:#f2f2f2;
  --row-alt:#f7f7f7;
  --ink:#2b2b2b;
  --ink-soft:#444;
  --nav:#555;
  --accent:#ff8a00;
  --pending:#d9360f;
  --rule:#cfcfcf;
}
*{box-sizing:border-box;margin:0;padding:0}
html,body{width:1200px;height:983px;overflow:hidden}
body{font-family:"Raleway",sans-serif;background:var(--page);color:var(--ink);position:relative}

.site-header{position:absolute;top:0;left:0;width:1200px;height:104px;background:var(--white)}
.brand{position:absolute;left:75px;top:30px;display:flex;align-items:center;gap:10px;font-size:34px;font-weight:700;color:var(--brand);letter-spacing:1px}
.brand-dot{width:22px;height:22px;border-radius:50%;background:var(--brand)}
.main-nav{position:absolute;left:0;top:0;height:104px;width:100%}
.nav-link{position:absolute;top:0;height:104px;line-height:104px;font-size:14px;font-weight:600;color:var(--nav);letter-spacing:.2px;text-decoration:none}
.nav-book{left:582px}
.nav-how{left:655px}
.nav-driver{left:774px;width:156px;background:var(--brand);color:var(--white);text-align:center}
.account{position:absolute;left:962px;top:34px;width:166px;height:36px;background:#f0f0f0;border-radius:2px;font-size:14px;color:var(--ink);line-height:36px;padding-left:13px}
.account svg{position:absolute;right:12px;top:14px}

.panel{position:absolute;left:75px;width:1051px;background:var(--white);border-radius:2px}
.panel-head{height:53px;background:var(--brand);color:var(--white);display:flex;align-items:center;padding-left:21px;gap:16px;font-size:21px;font-weight:600;letter-spacing:.4px;border-radius:2px 2px 0 0}
.booking{top:147px;height:342px}
.drivers{top:510px;height:356px}

.field-label{position:absolute;font-size:13px;font-weight:700;color:var(--ink);letter-spacing:.2px}
.field{position:absolute;background:var(--field);border-radius:2px;font-size:14px;color:var(--ink-soft);padding:0 22px;display:flex;align-items:center}
.field svg{position:absolute;right:19px}
.field-package{left:28px;top:101px;width:484px;height:46px}
.field-time{left:539px;top:101px;width:484px;height:46px}
.field-desc{left:28px;top:189px;width:995px;height:85px;align-items:flex-start;padding-top:16px}
.btn-update{position:absolute;left:28px;top:283px;width:117px;height:36px;background:var(--accent);color:var(--white);font-size:13px;font-weight:700;letter-spacing:.3px;display:flex;align-items:center;justify-content:center;border-radius:2px}

.notice{height:55px;background:var(--brand-soft);font-style:italic;font-size:14.5px;font-weight:500;color:#333;padding-left:25px;display:flex;align-items:center}
.driver-table{width:100%;border-collapse:collapse;font-size:13.5px}
.driver-table th{height:53px;text-align:left;font-weight:700;font-size:13px;letter-spacing:.2px;color:var(--ink);border-bottom:1px solid var(--rule)}
.driver-table td{height:49px;color:var(--ink-soft)}
.driver-table tbody tr:nth-child(even){background:var(--row-alt)}
.col-name{padding-left:25px;width:291px}
.col-dist{width:199px}
.col-time{width:266px}
.status{color:var(--pending);font-weight:700}

.site-footer{position:absolute;left:0;top:908px;width:1200px;height:75px;background:var(--white);text-align:center;font-size:12px;color:#555;line-height:84px}
</style>
</head>
<body>
<header class="site-header">
  <div class="brand"><span class="brand-dot"></span>Haulvane</div>
  <nav class="main-nav">
    <a class="nav-link nav-book" href="#">BOOK</a>
    <a class="nav-link nav-how" href="#">HOW IT WORKS</a>
    <a class="nav-link nav-driver" href="#">BECOME A DRIVER</a>
  </nav>
  <div class="account">ellis@mailvoro.com
    <svg width="9" height="6" viewBox="0 0 9 6"><path d="M1 1l3.5 3.5L8 1" fill="none" stroke="#333" stroke-width="1.5"/></svg>
  </div>
</header>

<section class="panel booking">
  <div class="panel-head">
    <svg width="19" height="19" viewBox="0 0 19 19"><rect x="0" y="0" width="19" height="19" rx="3" fill="#fff"/><path d="M5 14l.6-2.8 6-6 2.2 2.2-6 6z" fill="#4bc8f4"/></svg>
    BOOKING DETAILS
  </div>
  <div class="field-label" style="left:28px;top:84px">PACKAGE SELECTED</div>
  <div class="field field-package">Package 1
    <svg width="8" height="12" viewBox="0 0 8 12"><path d="M4 0l4 5H0zM4 12L0 7h8z" fill="#333"/></svg>
  </div>
  <div class="field-label" style="left:539px;top:84px">PICK UP TIME SELECTED</div>
  <div class="field field-time">July 18 at 14:31am
    <svg width="12" height="13" viewBox="0 0 12 13"><rect x=".5" y="2" width="11" height="10.5" fill="none" stroke="#444"/><rect x=".5" y="2" width="11" height="2.5" fill="#444"/><path d="M3 0v3M9 0v3M3 7h1M6 7h1M9 7h1M3 9.5h1M6 9.5h1M9 9.5h1" stroke="#444"/></svg>
  </div>
  <div class="field-label" style="left:28px;top:172px">DESCRIPTION</div>
  <div class="field field-desc">1 Large Stove</div>
  <div class="btn-update">UPDATE</div>
</section>

<section class="panel drivers">
  <div class="panel-head">
    <svg width="24" height="19" viewBox="0 0 24 19"><path d="M5 2.5Q5.6 1 7.3 1h9.4q1.7 0 2.3 1.5L21 8h1.5q1.5 0 1.5 1.5V15h-2v3h-4v-3H6v3H2v-3H0V9.5Q0 8 1.5 8H3z" fill="#fff"/><path d="M5.5 8l1.6-4.5h9.8L18.5 8z" fill="#4bc8f4"/><circle cx="4.5" cy="11.5" r="1.7" fill="#4bc8f4"/><circle cx="19.5" cy="11.5" r="1.7" fill="#4bc8f4"/></svg>
    DRIVERS IN YOUR AREA
  </div>
  <div class="notice">Please stay on this page and be patient, while we contact the drivers and find you on ASAP.</div>
  <table class="driver-table">
    <thead><tr><th class="col-name">NAME</th><th class="col-dist">DISTANCE</th><th class="col-time">AGREED PICK UP TIME</th><th></th></tr></thead>
    <tbody>
      <tr><td class="col-name">Dorian Pell</td><td>4.04km away</td><td>-</td><td class="status">Pending</td></tr>
      <tr><td class="col-name">Marcus Levet</td><td>5.07km away</td><td>-</td><td class="status">Pending</td></tr>
      <tr><td class="col-name">Calder Wynn</td><td>11.13km away</td><td>-</td><td class="status">Pending</td></tr>
      <tr><td class="col-name">Rowan Fitch</td><td>11.19km away</td><td>-</td><td class="status">Pending</td></tr>
    </tbody>
  </table>
</section>

<footer class="site-footer">Copyright © 2017. Company Name. All Right Reserved</footer>
</body>
</html>
```